Webdesign für für einen Shopware 5 Shop für eine Outdoormarke
Zielgruppe
Wir verkaufen Bergschuhe und Badehosen unter der Marke Brisal Tolvek. Hauptsächlich handelt es sich um Outdoorprodukte.
Aufgabenstellung
Wir möchten einen Brisal Tolvek Outdoor und Bademoden Shop aufbauen. Das Template sollte auf Shopware 5 aufgebaut sein.
Die webseite sollte Modern sein und viele Bildelemente enthalten. (Bilder sind vorhanden)
Wir möchten ein Design das man für den Outdoorbereich und für den Bademodenbreich verwenden kann.
Im Fokus soll die Seite unser Unternehmen bzw. Marke präsentieren. Im zweiten Schritt möchten wir unsere Ware dort verkaufen.
https://www.velorix-beispiel.ch/

```html
<!DOCTYPE html>
<html lang="de">
<head>
<meta charset="utf-8">
<title>Brisal Tolvek – Outdoor &amp; Bademode</title>
<link href="https://fonts.googleapis.com/css2?family=Yanone+Kaffeesatz:wght@400;500&family=Kalam:wght@400&family=Open+Sans:wght@400;600&display=swap" rel="stylesheet">
<style>
:root{
  --sidebar:#2b2d2a;
  --orange:#e5620c;
  --dark-box:#30312e;
  --panel-light:#f3f3f3;
  --panel-blue:#e8eaee;
  --text:#2a2a2a;
  --muted:#4a4a4a;
  --white:#ffffff;
  --footer:#4b6475;
  --footer-line:#8aa0ae;
  --overlay:rgba(40,40,40,.78);
}
*{margin:0;padding:0;box-sizing:border-box}
html,body{width:1200px;height:4959px;overflow:hidden}
body{position:relative;font-family:"Open Sans",Arial,sans-serif;color:var(--text);background:#fff}
.abs{position:absolute}
.head{font-family:"Yanone Kaffeesatz","Arial Narrow",sans-serif;font-weight:500;line-height:1.1}
.script{font-family:"Kalam",cursive}
.body-text{font-size:11.5px;line-height:1.45;color:var(--muted)}
.body-text p+p{margin-top:10px}
.photo{position:absolute}
.btn{position:absolute;background:var(--orange);color:#fff;font-family:"Yanone Kaffeesatz",sans-serif;font-size:25px;padding:4px 16px;border-radius:3px;white-space:nowrap}
.more{position:absolute;font-family:"Yanone Kaffeesatz",sans-serif;font-size:24px;color:#333}
.more::before{content:"";display:inline-block;border-left:9px solid var(--orange);border-top:7px solid transparent;border-bottom:7px solid transparent;margin-right:12px;vertical-align:1px}

/* sidebar */
.sidebar{left:0;top:0;width:280px;height:4959px;background:var(--sidebar)}
.brand{position:absolute;left:112px;top:80px;display:flex;align-items:center;gap:8px;color:#fff;font-family:"Yanone Kaffeesatz",sans-serif;font-size:19px;white-space:nowrap}
.brand-dot{width:34px;height:34px;border-radius:50%;background:#fff}
.main-nav{position:absolute;left:112px;top:170px;list-style:none}
.main-nav li{font-family:"Yanone Kaffeesatz",sans-serif;font-size:24px;color:#fff;height:49px}
.social{position:absolute;left:110px;top:545px;display:flex;gap:7px}
.social span{width:30px;height:30px;border-radius:50%;background:#c9c9c9}
.social span.rss{background:var(--orange)}
.account{position:absolute;left:112px;top:624px;font-size:11px;color:#ddd;white-space:nowrap}

/* footer */
.footer{left:280px;top:4584px;width:920px;height:375px;background:var(--footer);color:#fff}
.f-col{position:absolute;top:40px}
.f-col h4{font-family:"Yanone Kaffeesatz",sans-serif;font-weight:400;font-size:21px;padding-bottom:6px;border-bottom:1px solid var(--footer-line);margin-bottom:10px}
.f-col li{list-style:none;font-size:11px;line-height:23px;white-space:nowrap}
.f-col li::before{content:"› ";color:#fff}
.f-col.contact li::before{content:""}
.pay{position:absolute;top:292px;height:30px;border-radius:3px;background:#dfe6eb}
.seal{position:absolute;top:290px;width:34px;height:34px;border-radius:50%;background:#e6c84a}
.legal{position:absolute;top:359px;font-size:9.5px;color:#e6ecf0;white-space:nowrap}
</style>
</head>
<body>

<aside class="sidebar abs">
  <div class="brand"><span class="brand-dot"></span>BRISAL TOLVEK</div>
  <ul class="main-nav">
    <li>Männer</li><li>Frauen</li><li>Outdoor</li><li>Swimming</li><li>News</li><li>Shop</li><li>Kontakt</li>
  </ul>
  <div class="social"><span></span><span></span><span></span><span class="rss"></span></div>
  <div class="account">&#9679; Anmelden &nbsp;|&nbsp; Registrieren</div>
</aside>

<!-- hero -->
<section class="abs" style="left:280px;top:0;width:920px;height:449px">
  <div class="photo" role="img" aria-label="Schwimmer im Meer vor einer Felsküste" style="inset:0;background:linear-gradient(180deg,#b9c8d4 0%,#8ea4b6 40%,#4f6e86 55%,#6f8ea4 100%)"></div>
  <h1 class="abs head" style="left:0;width:880px;top:130px;text-align:center;color:#fff;font-size:48px">ABTAUCHEN</h1>
  <p class="abs head" style="left:0;width:880px;top:222px;text-align:center;color:#fff;font-size:32px;font-weight:400">sit amet, consectetur adipisicing elit</p>
  <div class="btn" style="left:383px;top:296px">Call to Action</div>
  <div class="abs" style="left:880px;top:69px;width:40px;height:37px;background:#8a9aa6"></div>
  <div class="abs" style="left:880px;top:116px;width:40px;height:38px;background:var(--orange)"></div>
</section>

<!-- wave band -->
<section class="abs" style="left:280px;top:449px;width:920px;height:229px">
  <div class="photo" role="img" aria-label="Brechende Welle" style="left:0;top:0;width:689px;height:229px;background:linear-gradient(160deg,#2b5a8c,#1f4770 50%,#6f9bc0)"></div>
  <p class="abs script" style="left:20px;top:96px;width:660px;color:#fff;font-size:28px;line-height:1.3;transform:rotate(-3deg)">Lorem ipsum dolor sit amet,<br>consectetur adipisicing elit, sed do eiusmod tempor</p>
  <div class="abs" style="left:689px;top:0;width:231px;height:229px;background:var(--dark-box);padding:30px 24px;color:#fff">
    <h3 class="head" style="font-size:28px">Lorem ipsum dolor sit amet</h3>
    <p style="font-size:11px;line-height:1.35;margin-top:12px;color:#ddd">consectetur adipisicing elit, sed do eiusmod tempor incididunt ut labore et dolore magna aliqua. Ut enim ad minim ...</p>
  </div>
</section>

<!-- surfers -->
<section class="abs" style="left:280px;top:678px;width:920px;height:676px">
  <div class="abs" style="left:0;top:0;width:230px;height:676px;background:var(--panel-light)"></div>
  <div class="photo" role="img" aria-label="Zwei Surfer mit Surfbrett am Strand" style="left:230px;top:0;width:690px;height:676px;background:linear-gradient(180deg,#c9cfd6 0%,#b5aea4 45%,#d9c9bd 100%)"></div>
  <div class="abs" style="left:230px;top:318px;border-left:18px solid var(--panel-light);border-top:20px solid transparent;border-bottom:20px solid transparent"></div>
  <h3 class="abs head" style="left:26px;top:250px;font-size:28px">Aenean<br>commodo ligula</h3>
  <p class="abs body-text" style="left:26px;top:330px;width:180px">Lorem ipsum dolor sit amet, consectetuer adipiscing elit. Aenean commodo ligula eget dolor. Aenean massa. Cum sociis natoque penatibus et</p>
  <div class="btn" style="left:26px;top:460px">Call to Action</div>
</section>

<!-- article -->
<section class="abs" style="left:280px;top:1354px;width:920px;height:356px;background:var(--panel-blue)">
  <div class="photo" role="img" aria-label="Surfer in Badeshorts mit Surfbrett" style="left:0;top:0;width:230px;height:356px;background:linear-gradient(180deg,#8a7f74,#a08c7d 50%,#c9bfb3)"></div>
  <h3 class="abs head" style="left:256px;top:50px;width:300px;font-size:28px">Lorem ipsum dolor sit amet, consectetur adipisicing elit</h3>
  <div class="abs body-text" style="left:256px;top:132px;width:300px">
    <p>Sed do eiusmod tempor incididunt ut labore et dolore magna aliqua. Ut enim ad minim veniam, quis nostrud exercitation ullamco laboris nisi ut aliquip ex ea commodo consequat.</p>
    <p>Duis aute irure dolor in reprehenderit in voluptate velit esse cillum dolore eu fugiat nulla pariatur. Excepteur sint occaecat cupidatat non proident, sunt in culpa qui officia deserunt mollit anim id est laborum.</p>
    <p>Sed ut perspiciatis unde omnis iste natus error sit voluptatem accusantium doloremque laudantium,</p>
  </div>
  <div class="abs body-text" style="left:604px;top:50px;width:296px">
    <p>Sed do eiusmod tempor incididunt ut labore et dolore magna aliqua. Ut enim ad minim veniam, quis nostrud exercitation ullamco laboris nisi ut aliquip ex ea commodo consequat.</p>
    <p>Duis aute irure dolor in reprehenderit in voluptate velit esse cillum dolore eu fugiat nulla pariatur. Excepteur sint occaecat cupidatat non proident, sunt in culpa qui officia deserunt mollit anim id est laborum.</p>
    <p>Sed ut perspiciatis unde omnis iste natus error sit voluptatem accusantium doloremque laudantium, totam rem aperiam, eaque ipsa quae ab illo inventore veritatis et quasi architecto beatae vitae dicta sunt explicabo.</p>
  </div>
  <div class="more" style="left:608px;top:302px">mehr</div>
</section>

<!-- sunset banner -->
<section class="abs" style="left:280px;top:1710px;width:920px;height:337px">
  <div class="photo" role="img" aria-label="Surfer mit Brett im Sonnenuntergang am Meer" style="inset:0;background:linear-gradient(180deg,#e07a1e 0%,#f2a33a 45%,#8a4a3a 70%,#3a2a3c 100%)"></div>
  <div class="abs" style="left:700px;top:44px;display:flex;align-items:center;gap:8px;font-family:'Yanone Kaffeesatz',sans-serif;font-size:20px;color:#1e1e1e;white-space:nowrap"><span style="width:34px;height:34px;border-radius:50%;background:#1e1e1e"></span>BRISAL TOLVEK</div>
  <p class="abs script" style="left:26px;top:228px;width:880px;color:#fff;font-size:28px;line-height:1.5">Lorem ipsum dolor sit amet, consectetur adipisicing elit, sed do eius-<br>mod tempor incididunt ut labore et dolore magna aliqua.</p>
</section>

<!-- three models -->
<section class="abs" style="left:280px;top:2047px;width:920px;height:516px">
  <div class="photo" role="img" aria-label="Mann mit Sonnenbrille am Meer" style="left:0;top:0;width:304px;height:516px;background:linear-gradient(180deg,#b7c6d2,#9aa7ae 50%,#6d7c8a)"></div>
  <div class="photo" role="img" aria-label="Mann mit Surfbrett am Strand sitzend" style="left:304px;top:0;width:304px;height:516px;background:linear-gradient(180deg,#6aa89a,#b9a08e 50%,#8b8f96)"></div>
  <div class="photo" role="img" aria-label="Mann trägt Surfbrett über dem Kopf" style="left:608px;top:0;width:312px;height:516px;background:linear-gradient(180deg,#d69a6c,#c9b6a6 40%,#9aa6b2)"></div>
  <div class="abs" style="left:0;top:399px;width:304px;height:117px;background:var(--overlay);color:#fff;text-align:center;padding-top:18px">
    <h3 class="head" style="font-size:28px">Lorem ipsum dolor sit<br>amet</h3></div>
  <div class="abs" style="left:304px;top:399px;width:304px;height:117px;background:var(--overlay);color:#fff;text-align:center;padding-top:18px">
    <h3 class="head" style="font-size:28px">Consectetur adipiscing<br>elit</h3></div>
  <div class="abs" style="left:608px;top:274px;width:312px;height:242px;background:var(--overlay);color:#fff;padding:28px 24px">
    <h3 class="head" style="font-size:28px">Sed do eiusmod</h3>
    <p style="font-size:11px;line-height:1.4;margin-top:12px;color:#ddd">tempor incididunt ut labore et dolore magna aliqua.</p>
    <p style="font-size:11px;line-height:1.4;margin-top:10px;color:#ddd">Ut enim ad minim veniam, quis nostrud exercitation ullamco laboris nisi ut aliquip ex ea commodo consequat.</p>
    <p style="font-size:11px;line-height:1.4;margin-top:10px;color:#ddd">Duis aute irure dolor in reprehenderit in.</p>
  </div>
</section>

<!-- hiking landscape + boots -->
<section class="abs" style="left:280px;top:2563px;width:920px;height:499px">
  <div class="photo" role="img" aria-label="Wanderer in grüner Küstenlandschaft" style="left:0;top:0;width:608px;height:297px;background:linear-gradient(180deg,#cfd6dc 0%,#7b8c5a 35%,#5a6b3a 70%,#8a7a4a)"></div>
  <div class="abs" style="left:0;top:297px;width:608px;height:202px;background:var(--panel-light)"></div>
  <h3 class="abs head" style="left:26px;top:326px;font-size:28px">Ut enim ad minim veniam, quis nostrud</h3>
  <div class="abs body-text" style="left:26px;top:368px;width:560px">
    <p>Exercitation ullamco laboris nisi ut aliquip ex ea commodo consequat. Duis aute irure dolor in reprehenderit in voluptate velit esse cillum dolore eu fugiat nulla pariatur.</p>
    <p>Excepteur sint occaecat cupidatat non proident, sunt in culpa qui officia deserunt mollit anim.</p>
  </div>
  <div class="more" style="left:30px;top:456px">mehr</div>
  <div class="photo" role="img" aria-label="Hände halten ein Paar Wanderschuhe" style="left:608px;top:0;width:312px;height:499px;background:linear-gradient(180deg,#d8c9b9,#7a7f84 45%,#4a5058)"></div>
  <div class="abs" style="left:608px;top:364px;width:312px;height:135px;background:var(--overlay);color:#fff;padding:22px 26px">
    <h3 class="head" style="font-size:28px">Tempor incididunt.</h3>
    <p style="font-size:11px;line-height:1.4;margin-top:8px;color:#ddd">Ut enim ad minim veniam, quis nostrud exercitation ullamco laboris nisi ut aliquip ex ea commodo consequat.</p>
  </div>
</section>

<!-- shoe on log -->
<section class="abs" style="left:280px;top:3062px;width:920px;height:299px;background:var(--panel-blue)">
  <div class="photo" role="img" aria-label="Wanderschuh tritt auf einen Baumstamm" style="left:0;top:0;width:458px;height:299px;background:linear-gradient(160deg,#4d4a32,#8a7a5a 50%,#3e3a2a)"></div>
  <h3 class="abs head" style="left:482px;top:30px;font-size:28px">Do incididunt ut labore et dolore magna</h3>
  <div class="abs body-text" style="left:482px;top:74px;width:400px">
    <p>Aliqua. ut enim ad minim veniam, quis nostrud exercitation ullamco laboris nisi.</p>
    <p>Ut aliquip ex ea commodo consequat.<br>Duis aute irure dolor in reprehenderit.</p>
    <p>in voluptate velit esse cillum dolore eu fugiat nulla pariatur. Excepteur sint occaecat cupidatat non proident, sunt in culpa qui officia deserunt mollit anim id est laborum.</p>
  </div>
  <div class="more" style="left:486px;top:242px">mehr</div>
</section>

<!-- woman on rocks -->
<section class="abs" style="left:280px;top:3361px;width:920px;height:298px">
  <div class="abs" style="left:0;top:0;width:458px;height:298px;background:#dfe3e8"></div>
  <div class="photo" role="img" aria-label="Wanderin sitzt auf Felsen im Wald" style="left:458px;top:0;width:462px;height:298px;background:linear-gradient(180deg,#9a8e6a,#6a6248 50%,#8a7a62)"></div>
  <div class="abs" style="left:458px;top:128px;border-left:18px solid #dfe3e8;border-top:20px solid transparent;border-bottom:20px solid transparent"></div>
  <h3 class="abs head" style="left:26px;top:46px;width:260px;font-size:28px">Aliqua. ut enim ad minim veniam.</h3>
  <div class="abs body-text" style="left:26px;top:138px;width:300px">
    <p>Quis nostrud exercitation ullamco laboris nisi.</p>
    <p>Ut aliquip ex ea commodo consequat. Duis aute irure dolor in reprehenderit.</p>
  </div>
  <div class="more" style="left:22px;top:240px">mehr</div>
</section>

<!-- boot close-up -->
<section class="abs" style="left:280px;top:3659px;width:920px;height:299px;background:var(--panel-blue)">
  <div class="photo" role="img" aria-label="Nahaufnahme eines Wanderschuhs auf Holz" style="left:0;top:0;width:458px;height:299px;background:linear-gradient(160deg,#2e3a22,#6a5a3a 50%,#3a3420)"></div>
  <h3 class="abs head" style="left:482px;top:36px;width:200px;font-size:28px">Quis nostrud exer-<br>citation.</h3>
  <div class="abs body-text" style="left:482px;top:118px;width:180px">
    <p>Ut aliquip ex ea commodo consequat. Duis aute irure dolor in reprehenderit.</p>
    <p>in voluptate velit esse cillum dolore eu fugiat nulla pariatur.</p>
    <p>Excepteur sint occaecat cupidatat non proident, sunt in culpa qui officia deserunt mollit anim</p>
  </div>
  <div class="abs body-text" style="left:714px;top:36px;width:190px">
    <p>Ut aliquip ex ea commodo consequat. Duis aute irure dolor in reprehenderit.</p>
    <h4 class="head" style="font-size:20px;color:var(--text);margin-top:10px">Voluptate velit esse cillum dolore eu fugiat nulla pariatur.</h4>
    <p>Excepteur sint occaecat cupidatat non proident, sunt in culpa. Qui officia deserunt mollit anim id est laborum.</p>
    <p>Sed ut perspiciatis unde omnis iste natus error sit voluptatem</p>
  </div>
</section>

<!-- forest strip -->
<section class="abs" style="left:280px;top:3958px;width:920px;height:231px">
  <div class="photo" role="img" aria-label="Dunkler Waldboden" style="left:0;top:0;width:230px;height:231px;background:linear-gradient(180deg,#3a3226,#5a4a36)"></div>
  <div class="photo" role="img" aria-label="Wasserfall im grünen Wald" style="left:230px;top:0;width:230px;height:231px;background:linear-gradient(180deg,#2a3a22,#6a8a4a 50%,#c8d0c8 60%,#3a5a2a)"></div>
  <div class="photo" role="img" aria-label="Sonnenlicht im dichten Wald" style="left:460px;top:0;width:230px;height:231px;background:linear-gradient(180deg,#2a3020,#7a7a3a 50%,#3a3a22)"></div>
  <div class="photo" role="img" aria-label="Moosiger Waldweg" style="left:690px;top:0;width:230px;height:231px;background:linear-gradient(180deg,#4a5a32,#3a4a28 60%,#5a4a30)"></div>
</section>

<!-- newsletter -->
<section class="abs" style="left:280px;top:4189px;width:920px;height:395px">
  <div class="photo" role="img" aria-label="Person vor einem wilden Fluss" style="inset:0;background:linear-gradient(180deg,#4a7390 0%,#3f6a86 50%,#6a8aa0 75%,#2f5068)"></div>
  <h2 class="abs head" style="left:0;width:920px;top:78px;text-align:center;color:#fff;font-size:38px">Nichts verpassen und den Newsletter abonnieren</h2>
  <div class="abs" style="left:280px;top:178px;width:335px;height:34px;background:#fff;border:1px solid #ccc;font-size:13px;font-style:italic;color:#999;padding:8px 12px">Ihre E-Mailadresse</div>
  <div class="abs" style="left:635px;top:178px;width:36px;height:34px;background:var(--orange)">
    <svg width="36" height="34" viewBox="0 0 36 34"><path d="M10 17 L27 9 L22 26 L18 19 Z" fill="#fff"/></svg>
  </div>
</section>

<!-- footer -->
<footer class="footer abs">
  <div class="f-col" style="left:48px;width:176px"><h4>Rechtliches</h4><ul>
    <li>Zahlungsmethoden</li><li>Versandmethoden</li><li>Datenschutzbelehrung</li><li>Impressum</li><li>Widerrufsbelehrung</li><li>Allgemeine Geschäftsbedingungen</li></ul></div>
  <div class="f-col" style="left:286px;width:160px"><h4>Service</h4><ul>
    <li>Blog</li><li>Über uns</li><li>Produktinfos</li><li>Userstories</li><li>Sale &amp; Bestseller</li><li>Geschenkgutscheine</li></ul></div>
  <div class="f-col" style="left:488px;width:150px"><h4>Ihr Account</h4><ul>
    <li>Bestellstatus</li><li>Bestellhistorie</li><li>Wunschliste</li><li>Passwort vergessen?</li><li>Daten ändern</li><li>Newsletter bestellen</li></ul></div>
  <div class="f-col contact" style="left:664px;width:190px"><h4>Kontakt</h4><ul>
    <li>Brisal Tolvek Outdoormode</li><li>Talgasse 7</li><li>54321 Beispielstadt</li><li>Beratung 0300 | 987 654 321</li><li>E-Mail: info [at] brisaltolvek.de</li></ul></div>
  <div class="pay" style="left:50px;width:30px"></div>
  <div class="pay" style="left:112px;width:76px"></div>
  <div class="pay" style="left:230px;width:40px"></div>
  <div class="pay" style="left:290px;width:84px"></div>
  <div class="pay" style="left:408px;width:92px"></div>
  <div class="seal" style="left:676px"></div>
  <div class="seal" style="left:718px;background:#f2f2f2"></div>
  <div class="seal" style="left:760px;background:#c7c79a"></div>
  <div class="seal" style="left:802px;background:#d8d24a"></div>
  <div class="legal" style="left:50px">© 2016 brisaltolvek</div>
  <div class="legal" style="left:274px">Alle Preise inkl. der gesetzlichen MwSt. Die durchgestrichenen Preise entsprechen dem bisherigen Preis in diesem Online-Shop.</div>
</footer>

</body>
</html>
```